Hospitality project presentation

I am developing a hospitality project and I need to present to the developer an outstanding presentation highlighting the overall look and feel. I will provide the text and most of the pictures (not all of them) some pictures (copyright free) will hae to be provided by the designer. Maximum number of pages 15, and zoom calls with me to make some adjustment if needed.

Hospitality

• calibri light

• 15 slides
• Hospitality resort project look and feel

```html
<!DOCTYPE html>
<html lang="en">
<head>
<meta charset="utf-8">
<title>Hospitality Presentation – Slide Overview</title>
<link rel="stylesheet" href="https://fonts.googleapis.com/css2?family=Hanken+Grotesk:wght@400;500;700&display=swap">
<style>
  :root {
    --gold: #d3b12f;
    --ink: #262626;
    --charcoal: #2b2b2b;
    --board: #505050;
    --paper: #ffffff;
    --paper-soft: #f6f6f6;
    --text-light: #ffffff;
    --body-text: #2a2a2a;
  }
  * { box-sizing: border-box; margin: 0; padding: 0; }
  html, body { width: 1200px; height: 744px; overflow: hidden; background: var(--board); }
  body { font-family: "Hanken Grotesk", Arial, sans-serif; color: var(--body-text); }
  .board { position: relative; width: 1200px; height: 744px; background: var(--board); overflow: hidden; }
  .slide { position: absolute; overflow: hidden; }

  /* Footer bars */
  .footer-bar {
    position: absolute; height: 27px; background: var(--charcoal); color: var(--text-light);
    font-size: 10.5px; letter-spacing: 0.2px; display: flex; align-items: center; justify-content: flex-end;
  }
  .footer-bar .crumb { padding-right: 10px; }
  .footer-bar strong { font-weight: 700; }
  .footer-bar .page-no {
    background: var(--gold); height: 100%; width: 34px; display: flex; align-items: center; justify-content: center;
    font-weight: 700; font-size: 11px;
  }

  /* Slide 1 – Introduction */
  .slide-intro { left: 0; top: 0; width: 392px; height: 301px; background: var(--paper); }
  .slide-intro .photo {
    position: absolute; left: 63px; top: 0; width: 329px; height: 274px;
    background: linear-gradient(180deg, #e7e6e3 0%, #d9d6d1 45%, #a9896a 75%, #8a6a4c 100%);
  }
  .slide-intro .footer-bar { left: 63px; top: 274px; width: 329px; }

  /* Slide 2 – Features A */
  .slide-features { left: 418px; top: 0; width: 782px; height: 301px; background: var(--paper); }
  .values { position: absolute; left: 70px; top: 0; width: 290px; }
  .value { position: absolute; left: 0; width: 247px; }
  .value-title {
    display: flex; align-items: center; gap: 6px; color: var(--gold); font-weight: 700;
    font-size: 10.5px; letter-spacing: 0.4px; line-height: 1;
  }
  .value-title::after { content: ""; flex: 1; height: 1.5px; background: var(--gold); }
  .value p { font-size: 8.6px; line-height: 12px; margin-top: 5px; color: var(--body-text); width: 225px; }
  .value-trust { top: -4px; }
  .value-respect { top: 57px; }
  .value-integrity { top: 114px; }
  .value-quality { top: 173px; }
  .brand { position: absolute; left: 55px; top: 266px; display: flex; align-items: center; gap: 6px; }
  .brand-mark { width: 9px; height: 9px; background: var(--ink); }
  .brand-name { font-size: 14px; font-weight: 700; color: var(--ink); letter-spacing: 0.3px; line-height: 1; }
  .brand-sub { position: absolute; left: 55px; top: 283px; font-size: 5px; letter-spacing: 1.6px; color: #777; }
  .gold-band { position: absolute; left: 315px; top: 0; width: 71px; height: 301px; background: var(--gold); }
  .gold-band svg { position: absolute; inset: 0; }
  .slide-features .photo {
    position: absolute; left: 386px; top: 0; width: 396px; height: 274px;
    background: linear-gradient(180deg, #dfe0e0 0%, #cfcfcd 40%, #9d8b78 75%, #7d6a58 100%);
  }
  .slide-features .footer-bar { left: 386px; top: 274px; width: 396px; }

  /* Slide 3 – Location */
  .slide-location { left: 0; top: 328px; width: 392px; height: 416px; background: var(--paper-soft); }
  .location-panel { position: absolute; left: 56px; top: 0; width: 274px; height: 341px; background: var(--charcoal); }
  .location-rule { position: absolute; left: 0; top: 69px; width: 84px; height: 1.5px; background: var(--gold); }
  .location-title {
    position: absolute; left: 109px; top: 57px; color: var(--gold); font-size: 19.5px; font-weight: 500; line-height: 1.2;
  }
  .location-copy { position: absolute; left: 110px; top: 99px; width: 178px; color: var(--text-light); }
  .location-copy p { font-size: 8.8px; line-height: 12.2px; margin-bottom: 7px; }

  /* Slide 4 – Full Image A */
  .slide-full { left: 418px; top: 328px; width: 782px; height: 416px; }
  .slide-full .photo {
    position: absolute; inset: 0;
    background: linear-gradient(100deg, #e9ecee 0%, #dadcdc 35%, #cfc9c2 60%, #b4aca3 80%, #8f8a86 100%);
  }
  .full-rule { position: absolute; left: 0; top: 86px; width: 660px; height: 1.5px; background: var(--paper); }
  .full-tag {
    position: absolute; right: 0; top: 55px; height: 31px; padding: 0 6px 0 14px; background: var(--gold);
    color: var(--text-light); font-size: 19px; display: flex; align-items: center;
  }
  .info-card {
    position: absolute; left: 69px; top: 240px; width: 241px; height: 176px; background: rgba(255,255,255,0.86);
  }
  .info-item { position: absolute; left: 20px; width: 210px; display: flex; gap: 9px; }
  .info-item:nth-child(1) { top: 45px; }
  .info-item:nth-child(2) { top: 108px; }
  .info-icon { width: 24px; height: 24px; flex: none; margin-top: 3px; }
  .info-item h3 { font-size: 10px; font-weight: 700; color: #111; line-height: 1.2; }
  .info-item p { font-size: 6.8px; line-height: 10.5px; margin-top: 5px; color: #111; font-weight: 500; }
</style>
</head>
<body>
<main class="board">

  <section class="slide slide-intro" aria-label="Introduction slide">
    <div class="photo" role="img" aria-label="Photograph of a bright bedroom with an upholstered bed, lamps and a rug on a wooden floor"></div>
    <div class="footer-bar">
      <span class="crumb">Sample Hospitality Powerpoint &gt; <strong>Introdution</strong></span>
      <span class="page-no">01</span>
    </div>
  </section>

  <section class="slide slide-features" aria-label="Features A slide">
    <div class="values">
      <div class="value value-trust">
        <h2 class="value-title">TRUST</h2>
        <p>Vestibulum porta justo quis suscipit tempus. Donec eu turpis id urna venenatis fermentum. Mauris ut condimentum nisi iaculis venenatis.</p>
      </div>
      <div class="value value-respect">
        <h2 class="value-title">RESPECT</h2>
        <p>Fusce aliquet nisl a lectus posuere malesuada. Phasellus cursus felis id lacus fringilla, at pharetra nisl accumsan. Suspendisse luctus erat euismod orci.</p>
      </div>
      <div class="value value-integrity">
        <h2 class="value-title">INTEGRITY</h2>
        <p>Nulla non maximus dui. Praesent bibendum a ante ut vulputate. Ut imperdiet sed erat vel scelerisque. Praesent mollis nisi et ligula suscipit malesuada.</p>
      </div>
      <div class="value value-quality">
        <h2 class="value-title">QUALITY</h2>
        <p>Duis non fermentum est. Maecenas in est eu ipsum malesuada porttitor ac id felis. Nulla id lectus porta, semper quam nec, lacinia lacus.</p>
      </div>
    </div>

    <div class="brand">
      <span class="brand-mark"></span>
      <span class="brand-name">HAVENMERE</span>
    </div>
    <div class="brand-sub">SECONDARY TEXT</div>

    <div class="gold-band">
      <svg width="71" height="301" viewBox="0 0 71 301" aria-hidden="true">
        <line x1="35" y1="0" x2="35" y2="229" stroke="#262626" stroke-width="2"/>
        <circle cx="35" cy="229" r="4.5" fill="#262626"/>
        <g fill="#262626">
          <circle cx="35" cy="36" r="21"/>
          <circle cx="35" cy="96" r="21"/>
          <circle cx="35" cy="149" r="21"/>
          <circle cx="35" cy="203" r="21"/>
        </g>
        <g fill="none" stroke="#d3b12f" stroke-width="1.6" stroke-linejoin="round" stroke-linecap="round">
          <!-- house -->
          <path d="M24 37 L35 26 L46 37 M27 34 V46 H43 V34 M32 46 V39 H38 V46"/>
          <!-- person with plus -->
          <circle cx="34" cy="90" r="5"/>
          <path d="M24 106 C24 99 29 96 34 96 C37 96 39 97 41 98"/>
          <path d="M42 101 V109 M38 105 H46"/>
          <!-- thumbs up -->
          <path d="M26 147 H30 V159 H26 Z M30 148 L35 140 C36 137 39 138 39 141 L38 145 H44 C46 145 47 147 46 149 L44 157 C43 159 42 159 41 159 H30"/>
          <!-- award -->
          <circle cx="35" cy="199" r="7"/>
          <path d="M30 205 L27 214 L31 212 L33 216 L35 206 M40 205 L43 214 L39 212 L37 216 L35 206"/>
        </g>
      </svg>
    </div>

    <div class="photo" role="img" aria-label="Photograph of a long hallway with wide-plank wooden floors leading to a dining area"></div>
    <div class="footer-bar">
      <span class="crumb">Sample Hospitality Powerpoint &gt; <strong>Features A</strong></span>
    </div>
  </section>

  <section class="slide slide-location" aria-label="Location slide">
    <div class="location-panel"></div>
    <div class="location-rule"></div>
    <h2 class="location-title">Location/Map/Plan</h2>
    <div class="location-copy">
      <p>Pellentesque habitant morbi tristique senectus et netus et malesuada fames ac turpis egestas. Sed eu lacinia mauris. Proin nisl odio, pellentesque quis nulla eget, lacoreet malesuada purus.</p>
      <p>Vestibulum velit lacus, pharetra quis faucibus nec, pellentesque in ex. Duis et libero tortor. Fusce sit amet tincidunt tortor, quis pharetra augue. Nulla id lectus porta, semper quam nec, lacinia lacus.</p>
      <p>Nulla porta turpis sed nisl euismod, quis elementum lectus facilisis. Mauris sed nunc et nulla varius malesuada. Sed luctus luctus posuere.</p>
    </div>
  </section>

  <section class="slide slide-full" aria-label="Full Image A slide">
    <div class="photo" role="img" aria-label="Photograph of a bright bathroom with a glass shower, tiled walls and a double vanity"></div>
    <div class="full-rule"></div>
    <div class="full-tag">Full Image A</div>
    <div class="info-card">
      <div class="info-item">
        <svg class="info-icon" viewBox="0 0 24 24" aria-hidden="true">
          <circle cx="12" cy="12" r="12" fill="#d3b12f"/>
          <path d="M17 12 H7 M11 8 L7 12 L11 16" fill="none" stroke="#fff" stroke-width="1.8" stroke-linecap="round" stroke-linejoin="round"/>
        </svg>
        <div>
          <h3>Sed luctus luctus posuere.</h3>
          <p>Pellentesque habitant morbi tristique senectus et netus et malesuada fames ac turpis egestas. Vestibulum velit lacus, pharetra quis ex.</p>
        </div>
      </div>
      <div class="info-item">
        <svg class="info-icon" viewBox="0 0 24 24" aria-hidden="true">
          <g fill="#d3b12f">
            <circle cx="12" cy="12" r="8"/>
            <rect x="10" y="0.5" width="4" height="5" rx="1"/>
            <rect x="10" y="18.5" width="4" height="5" rx="1"/>
            <rect x="0.5" y="10" width="5" height="4" rx="1"/>
            <rect x="18.5" y="10" width="5" height="4" rx="1"/>
            <rect x="10" y="0.5" width="4" height="5" rx="1" transform="rotate(45 12 12)"/>
            <rect x="10" y="0.5" width="4" height="5" rx="1" transform="rotate(135 12 12)"/>
            <rect x="10" y="0.5" width="4" height="5" rx="1" transform="rotate(225 12 12)"/>
            <rect x="10" y="0.5" width="4" height="5" rx="1" transform="rotate(315 12 12)"/>
          </g>
          <circle cx="12" cy="12" r="3.2" fill="#fff"/>
        </svg>
        <div>
          <h3>Sed luctus luctus posuere.</h3>
          <p>Pellentesque habitant morbi tristique senectus et netus et malesuada fames ac turpis egestas. Vestibulum velit lacus, pharetra quis ex.</p>
        </div>
      </div>
    </div>
  </section>

</main>
</body>
</html>
```